Health and Wellness company needs flyer to promote free seminar

Corvella Motion studio is a health and wellness company that offers an exercise program designed by physical therapists to help relieve pain and improve mobility. Our business is a new concept that is not well understood by the public. In order to promote our business we offer a free seminar where we present information regarding the underlying cause of pain and tightness. During the seminar we also perform a posture screen and movement testing for all participants.

Target Market(s)

Mostly healthy and active women ages 25-65

Industry/Entity Type

Health And Wellness

Font styles to use
Sans Serif

Colors

Designer to choose colors to be used in the design.

Requirements
Must have
• Title: Eliminate Pain and Tightness For Good
• Paragraph: Corvella Motion Studio offers a free 60 minute seminar: "The Busy Walker's Manual for Stretching and Living Lighter."
• What to Expect:
• • Identify the underlying cause of your pain and mobility issues
• • Expose what gets in the way of you moving and feeling better
• • Learn why traditional exercises don’t help and can actually make the problem worse
• • Reveal what your posture is saying and how that impacts you
• • Experience your muscle imbalances through movement tests
• • Discover the training method that realigns your posture, increases your mobility and reduces your pain
• Call to action: RSVP online at corvellamotionstudio.com
Nice to have
• Use a relevant image showing a female dealing with tightness in the low back, legs, etc.
• Emphasize that the seminar is FREE.
• Make the call to action prominent.

```html
<!DOCTYPE html>
<html lang="en">
<head>
<meta charset="utf-8">
<title>Corvella Motion Studio – Free Seminar Flyer</title>
<link rel="stylesheet" href="https://fonts.googleapis.com/css2?family=Bebas+Neue&family=Figtree:ital,wght@0,400;0,600;0,700;1,600&display=swap">
<style>
  :root {
    --purple: #4a4f9c;
    --purple-light: #5a5fb0;
    --orange: #f7931e;
    --orange-deep: #e8861a;
    --ink: #444444;
    --white: #ffffff;
    --stage: #d6d6d6;
    --photo-warm: #d99a80;
    --photo-rose: #e8909f;
  }
  * { box-sizing: border-box; margin: 0; padding: 0; }
  html, body { width: 1200px; height: 1200px; overflow: hidden; background: var(--stage); }
  .flyer {
    position: absolute; left: 160px; top: 30px;
    width: 986px; height: 1276px;
    transform: scale(0.8935); transform-origin: 0 0;
    background: var(--white);
    font-family: "Figtree", sans-serif;
    overflow: hidden;
  }
  .flyer-art { position: absolute; inset: 0; width: 986px; height: 1276px; }
  .brand {
    position: absolute; left: 537px; top: 62px;
    display: flex; align-items: center; gap: 14px;
  }
  .brand-mark { width: 54px; height: 54px; background: var(--orange); }
  .brand-name { font-weight: 700; font-size: 34px; color: var(--purple); letter-spacing: -0.5px; }
  .ribbon-label {
    position: absolute; left: 488px; top: 271px; width: 355px; height: 76px;
    display: flex; align-items: center; justify-content: center;
    font-style: italic; font-weight: 600; font-size: 56px; color: var(--white);
    padding-bottom: 6px;
  }
  .seminar-title {
    position: absolute; left: 393px; top: 380px; width: 540px;
    text-align: center; color: var(--white); font-weight: 400;
    font-family: "Bebas Neue", sans-serif; font-size: 52px; line-height: 60px;
  }
  .seminar-title span { display: block; white-space: nowrap; }
  .tagline {
    position: absolute; left: 0; top: 660px; width: 1010px; text-align: center;
    font-weight: 700; font-size: 31px; color: var(--white);
  }
  .expect-heading {
    position: absolute; left: 115px; top: 800px;
    font-family: "Bebas Neue", sans-serif; font-weight: 400; font-size: 36px; color: var(--purple);
  }
  .expect-list { position: absolute; left: 115px; top: 854px; width: 780px; list-style: none; }
  .expect-item { display: grid; grid-template-columns: 54px 139px 1fr; font-size: 19.5px; line-height: 32.5px; }
  .expect-item svg { margin-top: 8px; }
  .expect-verb { color: var(--orange); font-weight: 600; }
  .expect-text { color: var(--ink); }
  .rsvp-bar {
    position: absolute; left: 0; top: 1160px; width: 551px; height: 94px;
    background: var(--purple); border-radius: 0 14px 14px 0;
    padding: 14px 0 0 115px; color: var(--white); font-size: 27px; line-height: 35px;
  }
  .rsvp-url { font-weight: 700; }
  .free-badge {
    position: absolute; left: 584px; top: 1172px; width: 312px; height: 67px;
    border-top: 3px solid var(--orange); border-bottom: 3px solid var(--orange);
    display: flex; align-items: center; justify-content: center;
    font-size: 46px; color: var(--purple); white-space: nowrap;
  }
  .free-badge strong { font-weight: 700; margin-right: 12px; }
  .corner-tab {
    position: absolute; left: 929px; top: 1160px; width: 70px; height: 94px;
    background: var(--orange); border-radius: 14px 0 0 14px;
  }
</style>
</head>
<body>
<main class="flyer">
  <svg class="flyer-art" viewBox="0 0 986 1276">
    <defs>
      <linearGradient id="purpleWash" x1="0" y1="0" x2="1" y2="1">
        <stop offset="0" stop-color="#4a4f9c"/>
        <stop offset="0.55" stop-color="#565bad"/>
        <stop offset="1" stop-color="#484d98"/>
      </linearGradient>
      <linearGradient id="photoTone" x1="0" y1="0" x2="1" y2="1">
        <stop offset="0" stop-color="#d99a80"/>
        <stop offset="1" stop-color="#e8909f"/>
      </linearGradient>
    </defs>
    <path d="M0,40 C80,12 180,0 270,0 C430,120 700,200 986,170 L986,640 L0,640 Z" fill="url(#purpleWash)"/>
    <rect x="40" y="0" width="440" height="660" fill="url(#photoTone)" role="img" aria-label="Photo of an active woman seen from behind, hands pressed to her lower back in pain"/>
    <path d="M0,560 C250,620 600,660 986,605 L986,800 C700,720 300,720 0,780 Z" fill="var(--orange)"/>
    <path d="M0,620 C300,690 700,700 986,740 L986,800 C700,720 300,720 0,780 Z" fill="var(--orange-deep)" opacity="0.5"/>
    <path d="M0,560 C250,620 600,660 986,605" fill="none" stroke="#fff" stroke-width="5"/>
    <path d="M488,271 L843,271 L812,309 L843,347 L488,347 L519,309 Z" fill="var(--orange)"/>
  </svg>

  <div class="brand"><span class="brand-mark"></span><span class="brand-name">Corvella Motion Studio</span></div>
  <div class="ribbon-label">presents</div>
  <h1 class="seminar-title"><span>The Busy Walker's Manual</span><span>for Stretching and</span><span>Living Lighter</span></h1>
  <p class="tagline">Eliminate Pain and Tightness for Good.</p>

  <h2 class="expect-heading">What to expect:</h2>
  <ul class="expect-list">
    <li class="expect-item"><svg width="20" height="20" viewBox="0 0 20 20"><circle cx="10" cy="10" r="8" fill="none" stroke="#4a4f9c" stroke-width="2.4"/><path d="M6,10.2 L9,13 L14,7.5" fill="none" stroke="#4a4f9c" stroke-width="2.4"/></svg><span class="expect-verb">Identify</span><span class="expect-text">the underlying cause of your pain and mobility issues</span></li>
    <li class="expect-item"><svg width="20" height="20" viewBox="0 0 20 20"><circle cx="10" cy="10" r="8" fill="none" stroke="#4a4f9c" stroke-width="2.4"/><path d="M6,10.2 L9,13 L14,7.5" fill="none" stroke="#4a4f9c" stroke-width="2.4"/></svg><span class="expect-verb">Expose</span><span class="expect-text">what gets in the way of you moving and feeling better</span></li>
    <li class="expect-item"><svg width="20" height="20" viewBox="0 0 20 20"><circle cx="10" cy="10" r="8" fill="none" stroke="#4a4f9c" stroke-width="2.4"/><path d="M6,10.2 L9,13 L14,7.5" fill="none" stroke="#4a4f9c" stroke-width="2.4"/></svg><span class="expect-verb">Learn</span><span class="expect-text">why traditional exercises don’t help and can actually make the problem worse</span></li>
    <li class="expect-item"><svg width="20" height="20" viewBox="0 0 20 20"><circle cx="10" cy="10" r="8" fill="none" stroke="#4a4f9c" stroke-width="2.4"/><path d="M6,10.2 L9,13 L14,7.5" fill="none" stroke="#4a4f9c" stroke-width="2.4"/></svg><span class="expect-verb">Reveal</span><span class="expect-text">what your posture is saying and how that impacts you</span></li>
    <li class="expect-item"><svg width="20" height="20" viewBox="0 0 20 20"><circle cx="10" cy="10" r="8" fill="none" stroke="#4a4f9c" stroke-width="2.4"/><path d="M6,10.2 L9,13 L14,7.5" fill="none" stroke="#4a4f9c" stroke-width="2.4"/></svg><span class="expect-verb">Experience</span><span class="expect-text">your muscle imbalances through movement tests</span></li>
    <li class="expect-item"><svg width="20" height="20" viewBox="0 0 20 20"><circle cx="10" cy="10" r="8" fill="none" stroke="#4a4f9c" stroke-width="2.4"/><path d="M6,10.2 L9,13 L14,7.5" fill="none" stroke="#4a4f9c" stroke-width="2.4"/></svg><span class="expect-verb">Discover</span><span class="expect-text">the training method that realigns your posture, increases your mobility and reduces your pain</span></li>
  </ul>

  <div class="rsvp-bar">RSVP online at<br><span class="rsvp-url">corvellamotionstudio.com</span></div>
  <div class="free-badge"><strong>FREE</strong>Seminar</div>
  <div class="corner-tab"></div>
</main>
</body>
</html>
```